Bramwell Corner Sports Pub. Where the locals go!!

We are creating a sports pub. We are needing a fun website that offers our menu along with an event page and general info. We have some attached links that we really like:
https://www.dunmorrows.example/
https://www.cafepelindra.example/
https://www.quillstoneyx.example/
We are doing a pirate theme but that is because the area we are in. We would like to see a pirate like in our logo doing something like drinking real time similar to the dunmorrows website above.
Target Market(s)
Sports Fans
Industry/Entity Type
Pub, Bar, Restaurant
Coding
Coded - Design and coding required
Number of Pages Required
3 page
Font styles to use
Other font styles liked:
- see uploads
Look and feel

```html
<!DOCTYPE html>
<html lang="en">
<head>
<meta charset="utf-8">
<title>Bramwell Corner Sports Pub</title>
<link href="https://fonts.googleapis.com/css2?family=Poppins:wght@400;500;600;700&family=Rye&display=swap" rel="stylesheet">
<style>
:root{
  --tan:#d7b088;
  --tan-light:#e0bd97;
  --brown:#6a3a1c;
  --brown-text:#3b2513;
  --red:#c41e23;
  --red-dark:#a5151a;
  --orange:#ef8a12;
  --black:#0b0303;
  --white:#ffffff;
  --box-brown:#7b4a22;
}
*{margin:0;padding:0;box-sizing:border-box}
html,body{width:1200px;height:4271px;overflow:hidden}
body{position:relative;background:var(--tan);font-family:'Poppins',sans-serif;color:var(--brown-text)}
.abs{position:absolute}
.btn{position:absolute;display:flex;align-items:center;justify-content:center;background:var(--red);color:var(--white);font-weight:700;font-size:15px;border-radius:5px;text-transform:uppercase;box-shadow:0 3px 6px rgba(0,0,0,.25)}

/* header */
.site-header{position:absolute;left:0;top:0;width:1200px;height:88px;background:#dcb58d;z-index:3}
.brand-plate{position:absolute;left:0;top:0}
.brand{position:absolute;left:128px;top:30px;display:flex;align-items:center;gap:14px}
.brand-dot{width:28px;height:28px;border-radius:50%;background:var(--red)}
.brand-name{font-family:'Rye',serif;color:var(--white);font-size:15px;letter-spacing:1px}
.main-nav{position:absolute;top:34px;left:0;width:1200px}
.main-nav a{position:absolute;color:var(--white);font-size:15px;font-weight:600;text-decoration:none}

/* hero */
.hero-art{position:absolute;left:0;top:0;z-index:1}
.hero-title{left:113px;top:283px;z-index:2;color:var(--red);font-family:'Rye',serif;font-weight:400;font-size:46px;line-height:52px;letter-spacing:2px;
  text-shadow:-2px -2px 0 #fff,2px -2px 0 #fff,-2px 2px 0 #fff,2px 2px 0 #fff,0 2px 0 #fff,2px 0 0 #fff}
.hero-text{left:113px;top:406px;width:510px;z-index:2;color:var(--white);font-size:14px;line-height:29px}
.hero-btn{left:114px;top:538px;width:157px;height:50px;z-index:2}
.dots{position:absolute;display:flex;gap:6px;z-index:2}
.dot{border-radius:50%}

/* about */
.section-title{color:var(--brown);font-family:'Rye',serif;font-weight:400;font-size:36px;letter-spacing:2px}
.about-title{left:111px;top:922px}
.about-text{left:111px;top:984px;width:500px;font-size:14.5px;line-height:31px}
.about-btn{left:111px;top:1186px;width:134px;height:44px}
.ring{left:782px;top:933px;width:282px;height:282px;border-radius:50%;background:var(--red)}
.ring-photo{left:812px;top:963px;width:222px;height:222px;border-radius:50%;
  background:radial-gradient(circle at 40% 40%,#c9673a,#7a2d5a 55%,#2d1a3e)}
.ring-badge{left:726px;top:1058px;width:198px;height:198px;border-radius:50%;background:var(--white);box-shadow:0 2px 8px rgba(0,0,0,.3)}

/* menu */
.dark-band{position:absolute;left:0;top:1300px}
.menu-art{left:75px;top:1458px;width:541px;height:497px;border-radius:60px;
  background:radial-gradient(ellipse at center,#e4b982 0%,#d6a468 48%,#5fb6d4 70%,#2a6f8c 100%);
  display:flex;align-items:center;justify-content:center}
.menu-art span{font-family:'Rye',serif;color:#8a4a1f;font-size:34px;letter-spacing:2px}
.specials{left:671px;top:1528px;width:476px;height:353px;border:2px solid var(--white);border-radius:8px;color:var(--white)}
.specials h3{position:absolute;top:24px;width:100%;text-align:center;font-family:'Rye',serif;font-weight:400;font-size:24px;letter-spacing:2px}
.special-row{position:absolute;left:35px;right:18px;height:30px;display:flex;align-items:center}
.special-row .item{font-size:14px;width:128px}
.special-row .leader{width:186px;border-bottom:2px dotted var(--white);margin-top:8px}
.special-row .price{margin-left:auto;font-size:23px;font-weight:700}
.view-btn{left:850px;top:1922px;width:133px;height:43px}

/* events */
.events-title{left:0;top:2130px;width:1200px;text-align:center}
.events-intro{left:100px;top:2196px;width:1000px;text-align:center;font-size:15px;line-height:31px}
.event-photo{box-shadow:0 4px 10px rgba(0,0,0,.35)}
.photo-a{left:111px;top:2320px;width:499px;height:394px;background:linear-gradient(160deg,#2e4b3a,#513226 45%,#a1653f 80%,#3a2418)}
.photo-b{left:605px;top:2717px;width:499px;height:395px;background:linear-gradient(200deg,#8e2a1c,#b6523a 35%,#3d1f16 75%,#1c0f0b)}
.event-text{font-size:14.5px;line-height:31px}
.text-a{left:643px;top:2346px;width:440px}
.text-b{left:119px;top:2756px;width:440px}
.book-a{left:645px;top:2645px;width:132px;height:43px}
.book-b{left:121px;top:3054px;width:134px;height:42px}

/* reach out */
.footer-bg{left:0;top:3513px;width:1200px;height:758px;background:var(--black)}
.reach{left:109px;top:3253px;width:976px;height:525px;border-radius:6px;background:linear-gradient(180deg,#7f4d24,#72431d)}
.reach h2{position:absolute;top:34px;width:100%;text-align:center;font-family:'Rye',serif;font-weight:400;color:var(--white);font-size:34px;letter-spacing:3px}
.field{position:absolute;background:var(--white);font-size:15px;color:#333;padding:20px 30px}
.submit{left:96px;top:429px;width:135px;height:42px}

/* footer */
.foot-brand{left:111px;top:3860px;display:flex;align-items:center;gap:12px}
.foot-brand .brand-dot{width:32px;height:32px}
.foot-brand .brand-name{font-size:19px}
.socials{left:116px;top:3927px;display:flex;gap:10px}
.socials span{width:26px;height:26px;background:var(--white);border-radius:5px}
.newsletter{left:113px;top:3977px;width:348px;height:45px;display:flex}
.newsletter .input{flex:1;background:var(--white);font-size:15px;font-weight:600;color:#222;padding:12px 20px}
.newsletter .send{width:65px;background:var(--red);display:flex;align-items:center;justify-content:center}
.foot-head{font-family:'Rye',serif;color:var(--white);font-size:18px;letter-spacing:1px}
.quick-links{left:611px;top:3917px}
.quick-links a{position:absolute;left:0;white-space:nowrap;color:var(--white);font-size:15px;text-decoration:none}
.contact-item{position:absolute;left:872px;display:flex;gap:15px;color:var(--white);font-size:15px;line-height:20px}
.contact-icon{width:36px;height:32px;background:var(--white);display:flex;align-items:center;justify-content:center;flex:none}
.rule{left:108px;top:4212px;width:974px;height:1px;background:#bbb}
.copyright{left:0;top:4228px;width:1200px;text-align:center;color:var(--white);font-size:13.5px}
</style>
</head>
<body>

<header class="site-header">
  <svg class="brand-plate" width="460" height="88" viewBox="0 0 460 88"><polygon points="0,0 447,0 406,88 0,88" fill="var(--black)"/></svg>
  <div class="brand"><span class="brand-dot"></span><span class="brand-name">BRAMWELL CORNER SPORTS</span></div>
  <nav class="main-nav">
    <a style="left:516px">Home</a>
    <a style="left:601px">About Us</a>
    <a style="left:718px">Events</a>
    <a style="left:816px">Menu's</a>
    <a style="left:916px">Contact Us</a>
  </nav>
</header>

<svg class="hero-art" width="1200" height="870" viewBox="0 0 1200 870">
  <defs>
    <linearGradient id="heroPhoto" x1="0" y1="0" x2="1" y2="1">
      <stop offset="0" stop-color="#5a3316"/>
      <stop offset=".45" stop-color="#3b1e0d"/>
      <stop offset=".75" stop-color="#2a1409"/>
      <stop offset="1" stop-color="#160a05"/>
    </linearGradient>
  </defs>
  <polygon points="0,722 600,858 1200,722 1200,730 600,836 0,730" fill="var(--orange)"/>
  <g role="img" aria-label="Photo of the pub interior: long wooden bar, stools and screens">
    <polygon points="0,88 1200,88 1200,729 600,834 0,729" fill="url(#heroPhoto)"/>
  </g>
</svg>
<h1 class="abs hero-title">WELCOME TO<br>BRAMWELL CORNER SPORTS PUB</h1>
<p class="abs hero-text">Lorem ipsum dolor sit amet, consectetur adipiscing elit, sed do eiusmod tempor incididunt ut labore et dolore magna aliqua. Ut enim ad minim veniam, quis nostrud exercitation ullamco laboris nisi ut aliquip ex ea commodo consequat</p>
<a class="btn hero-btn">Get Started</a>
<div class="dots" style="left:563px;top:640px">
  <span class="dot" style="width:20px;height:20px;background:#fff"></span>
  <span class="dot" style="width:20px;height:20px;background:var(--red)"></span>
  <span class="dot" style="width:20px;height:20px;background:#fff"></span>
</div>

<h2 class="abs section-title about-title">ABOUT US</h2>
<p class="abs about-text">Lorem ipsum dolor sit amet, consectetur adipiscing elit, sed do eiusmod tempor incididunt ut labore et dolore magna aliqua. Ut enim ad minim veniam, quis nostrud exercitation ullamco laboris nisi ut aliquip ex ea commodo consequat. Duis aute irure dolor in reprehenderit in voluptate velit esse cillum dolore eu fugiat nulla pariatur.</p>
<a class="btn about-btn">Read More</a>
<div class="abs ring"></div>
<div class="abs ring-photo" role="img" aria-label="Photo of the colourful pub ceiling and walls"></div>
<div class="abs ring-badge"></div>

<svg class="dark-band" width="1200" height="735" viewBox="0 1300 1200 735">
  <polygon points="0,1436 600,1311 1200,1436 1200,1442 600,1327 0,1442" fill="var(--orange)"/>
  <polygon points="0,1442 600,1327 1200,1442 1200,2035 0,2035" fill="var(--black)"/>
</svg>
<div class="abs menu-art" role="img" aria-label="Pirate illustration: parchment scroll with ship wheel, parrot, barrel, anchor and waves"><span>OUR MENU'S</span></div>
<div class="abs specials">
  <h3>SPECIALS</h3>
  <div class="special-row" style="top:102px"><span class="item">LOREM IPSUM</span><span class="leader"></span><span class="price">$250</span></div>
  <div class="special-row" style="top:154px"><span class="item">LOREM IPSUM</span><span class="leader"></span><span class="price">$350</span></div>
  <div class="special-row" style="top:205px"><span class="item">LOREM IPSUM</span><span class="leader"></span><span class="price">$400</span></div>
  <div class="special-row" style="top:257px"><span class="item">LOREM IPSUM</span><span class="leader"></span><span class="price">$500</span></div>
</div>
<a class="btn view-btn">View More</a>

<h2 class="abs section-title events-title">EVENTS</h2>
<p class="abs events-intro">Lorem ipsum dolor sit amet, consectetur adipiscing elit, sed do eiusmod tempor incididunt ut labore et dolore magna aliqua. Ut enim ad minim veniam, quis nostrud exercitation ullamco laboris nisi ut aliquip ex ea commodo consequat.</p>
<div class="abs event-photo photo-a" role="img" aria-label="Photo of fans cheering at the bar during a football game"></div>
<p class="abs event-text text-a">Lorem ipsum dolor sit amet, consectetur adipiscing elit, sed do eiusmod tempor incididunt ut labore et dolore magna aliqua. Ut enim ad minim veniam, quis nostrud exercitation ullamco laboris nisi ut aliquip ex ea commodo consequat. Duis aute irure dolor in reprehenderit in voluptate velit esse cillum dolore eu fugiat nulla pariatur. Excepteur sint occaecat cupidatat non proident, sunt in culpa qui officia deserunt mollit anim id est laborum.</p>
<a class="btn book-a">Book Event</a>
<div class="abs event-photo photo-b" role="img" aria-label="Photo of a crowded pub evening under red lights"></div>
<p class="abs event-text text-b">Lorem ipsum dolor sit amet, consectetur adipiscing elit, sed do eiusmod tempor incididunt ut labore et dolore magna aliqua. Ut enim ad minim veniam, quis nostrud exercitation ullamco laboris nisi ut aliquip ex ea commodo consequat. Duis aute irure dolor in reprehenderit in voluptate velit esse cillum dolore eu fugiat nulla pariatur. Excepteur sint occaecat cupidatat non proident, sunt in culpa qui officia deserunt mollit anim id est laborum.</p>
<a class="btn book-b">Book Event</a>
<div class="dots" style="left:569px;top:3147px">
  <span class="dot" style="width:16px;height:16px;background:var(--red);border:2px solid #5a1a10"></span>
  <span class="dot" style="width:16px;height:16px;background:#111;border:2px solid #5a1a10"></span>
  <span class="dot" style="width:16px;height:16px;background:var(--red);border:2px solid #5a1a10"></span>
</div>

<div class="abs footer-bg"></div>
<section class="abs reach">
  <h2>REACH OUT</h2>
  <div class="field" style="left:98px;top:114px;width:375px;height:60px">Name</div>
  <div class="field" style="left:491px;top:114px;width:373px;height:60px">Email*</div>
  <div class="field" style="left:98px;top:190px;width:767px;height:206px">Message</div>
  <a class="btn submit">Submit</a>
</section>

<div class="abs foot-brand"><span class="brand-dot"></span><span class="brand-name">BRAMWELL CORNER SPORTS PUB</span></div>
<div class="abs socials"><span></span><span></span><span></span><span></span></div>
<div class="abs newsletter">
  <div class="input">Email Address</div>
  <div class="send"><svg width="32" height="22" viewBox="0 0 32 22"><rect x="1" y="1" width="30" height="20" fill="none" stroke="#fff" stroke-width="2"/><polyline points="1,1 16,13 31,1" fill="none" stroke="#fff" stroke-width="2"/><line x1="1" y1="21" x2="12" y2="10" stroke="#fff" stroke-width="2"/><line x1="31" y1="21" x2="20" y2="10" stroke="#fff" stroke-width="2"/></svg></div>
</div>

<div class="abs foot-head" style="left:611px;top:3860px">QUICK LINKS</div>
<nav class="abs quick-links">
  <a style="top:-10px">Home</a>
  <a style="top:32px">Abut Us</a>
  <a style="top:73px">Events</a>
  <a style="top:115px">Menus's</a>
  <a style="top:156px">Cpntact us</a>
</nav>

<div class="abs foot-head" style="left:872px;top:3860px">CONTACT US</div>
<div class="contact-item" style="top:3915px">
  <span class="contact-icon"><svg width="18" height="20" viewBox="0 0 18 20"><path d="M9 1a6 6 0 0 0-6 6c0 4.5 6 11 6 11s6-6.5 6-11a6 6 0 0 0-6-6z" fill="#111"/><circle cx="9" cy="7" r="2.3" fill="#fff"/></svg></span>
  <span>482 Harbor Lane<br>Suite 210,MN 55012</span>
</div>
<div class="contact-item" style="top:3977px">
  <span class="contact-icon"><svg width="18" height="18" viewBox="0 0 18 18"><path d="M4 1l3 4-2 2c1 2.5 3.5 5 6 6l2-2 4 3-2 3C8 17 1 10 1 3z" fill="#111"/></svg></span>
  <span style="line-height:32px">+1 555 014 2290</span>
</div>
<div class="contact-item" style="top:4030px">
  <span class="contact-icon"><svg width="22" height="16" viewBox="0 0 22 16"><rect x="1" y="1" width="20" height="14" fill="none" stroke="#111" stroke-width="2"/><polyline points="1,1 11,9 21,1" fill="none" stroke="#111" stroke-width="2"/></svg></span>
  <span>info@bramwellcorner<br>pub.example</span>
</div>
<div class="contact-item" style="top:4088px">
  <span class="contact-icon"><svg width="20" height="20" viewBox="0 0 20 20"><circle cx="10" cy="10" r="9" fill="#111"/><polyline points="10,4 10,10 14,12" fill="none" stroke="#fff" stroke-width="2"/></svg></span>
  <span style="padding-top:10px;line-height:25px">HOURS<br>Mon-Fri &nbsp;&nbsp;10am -5pm<br>sat-Sun &nbsp;&nbsp;10am -10pm</span>
</div>

<div class="abs rule"></div>
<p class="abs copyright">Copyright © 2023 bramwell corner sports pub. All Rights Reserved.</p>

</body>
</html>
```